Automotive Accessories Business Card

Design a business template that match our new logo design and our industry.

https://www.qelmotorgear.com/

Target Market(s)

Aftermarket auto parts and accessories

Industry/Entity Type

automotive

Contact Information for Business Card

company logo

Font styles to use
Serif
Sans Serif

Colors
EB3D1F
EC4F4E
F09395
F8D3D4
FCEDEE

```html
<!DOCTYPE html>
<html lang="en">
<head>
<meta charset="utf-8">
<title>QEL Motor Gear – Business Card</title>
<link rel="stylesheet" href="https://fonts.googleapis.com/css2?family=Open+Sans:ital,wght@0,400;0,700;0,800;1,800&display=swap">
<style>
  :root {
    --canvas: #e9e7e4;
    --charcoal: #3a3a3b;
    --charcoal-deep: #2b2b2c;
    --charcoal-soft: #4a4a4b;
    --paper: #f3f3f3;
    --red: #d22a2e;
    --ink-light: #ffffff;
    --emboss: #5a5a5b;
  }
  * { box-sizing: border-box; margin: 0; padding: 0; }
  html, body {
    width: 1200px; height: 960px; overflow: hidden;
    background: var(--canvas);
    font-family: "Open Sans", Arial, sans-serif;
  }
  .canvas {
    position: relative; width: 1200px; height: 960px;
  }
  .card {
    position: absolute; left: 220px; width: 760px; height: 434px;
    box-shadow: 0 10px 28px rgba(0,0,0,.22);
    overflow: hidden;
  }
  .card--back {
    top: 38px;
    background: radial-gradient(ellipse at 40% 30%, var(--charcoal-soft), var(--charcoal-deep));
    display: flex; align-items: center; justify-content: center;
  }
  .card--front { top: 500px; background: var(--paper); }
  .card-art { position: absolute; inset: 0; }

  .wordmark {
    display: flex; align-items: center; gap: 14px;
    font-weight: 800; letter-spacing: 2px; text-transform: uppercase;
  }
  .wordmark-square { width: 22px; height: 22px; background: var(--red); flex: none; }
  .card--back .wordmark { color: var(--emboss); font-size: 52px; }
  .card--back .wordmark-square { background: var(--emboss); width: 28px; height: 28px; }
  .card--front .wordmark {
    position: absolute; left: 452px; top: 150px;
    color: var(--charcoal); font-size: 34px; line-height: 1.05;
    flex-direction: column; align-items: flex-start; gap: 8px;
  }
  .wordmark-row { display: flex; align-items: center; gap: 12px; }

  .holder {
    position: absolute; left: 30px; top: 58px; color: var(--ink-light);
  }
  .holder-name { font-weight: 800; font-style: italic; font-size: 30px; letter-spacing: .5px; text-transform: uppercase; }
  .holder-title { font-size: 18px; margin-top: -2px; }
  .contacts { list-style: none; margin-top: 30px; }
  .contacts li {
    display: flex; align-items: center; gap: 12px;
    font-size: 18px; line-height: 1; margin-bottom: 14px;
  }
  .contacts svg { width: 18px; height: 18px; flex: none; }
  .contacts b { font-weight: 800; font-style: italic; }
</style>
</head>
<body>
<main class="canvas">

  <section class="card card--back" aria-label="Card back">
    <div class="wordmark"><span class="wordmark-square"></span>QEL Motor Gear</div>
  </section>

  <section class="card card--front" aria-label="Card front">
    <svg class="card-art" viewBox="0 0 760 434" aria-hidden="true">
      <polygon points="0,0 213,0 595,404 16,404 0,388" fill="var(--charcoal)"/>
      <line x1="238" y1="0" x2="418" y2="190" stroke="var(--charcoal)" stroke-width="5"/>
      <line x1="22" y1="419" x2="330" y2="419" stroke="var(--red)" stroke-width="3"/>
      <polygon points="596,396 664,396 718,434 623,434" fill="var(--red)"/>
      <polygon points="718,434 760,434 760,404 736,404" fill="var(--charcoal)"/>
    </svg>

    <div class="holder">
      <h1 class="holder-name">Dana Whitlow</h1>
      <p class="holder-title">Sales Manager</p>
      <ul class="contacts">
        <li>
          <svg viewBox="0 0 24 24"><path fill="var(--red)" d="M6.6 10.8a15 15 0 0 0 6.6 6.6l2.2-2.2a1 1 0 0 1 1-.25 11.4 11.4 0 0 0 3.6.57 1 1 0 0 1 1 1V20a1 1 0 0 1-1 1A17 17 0 0 1 3 4a1 1 0 0 1 1-1h3.5a1 1 0 0 1 1 1c0 1.25.2 2.45.57 3.57a1 1 0 0 1-.25 1z"/></svg>
          1-800-555-0142
        </li>
        <li>
          <svg viewBox="0 0 24 24"><rect x="2" y="5" width="20" height="14" fill="var(--red)"/><path d="M2 5l10 8 10-8" fill="none" stroke="var(--charcoal)" stroke-width="1.6"/></svg>
          sales@qelmotorgear.com
        </li>
        <li>
          <svg viewBox="0 0 24 24"><circle cx="12" cy="12" r="10" fill="var(--red)"/><path d="M2 12h20M12 2c3 3 3 17 0 20M12 2c-3 3-3 17 0 20" fill="none" stroke="var(--charcoal)" stroke-width="1.4"/></svg>
          www.<b>qelmotorgear</b>.com
        </li>
      </ul>
    </div>

    <div class="wordmark">
      <div class="wordmark-row"><span class="wordmark-square"></span>QEL Motor</div>
      <div>Gear</div>
    </div>
  </section>

</main>
</body>
</html>
```